Professional looking Roller Blind Discount Card that portrays quality at a value for money price!

We need a double sided business card designed as a discount card. Size 90mm wide x 55mm high.We would like it to look professional and portray quality at a value for money price point.I have uploaded a word document with a basic layout with the information we want included on each side of the card. Please put your own thought into the layout.

Contact Information for Business Card

As per word document attached.

```html
<!DOCTYPE html>
<html lang="en">
<head>
<meta charset="utf-8">
<title>Roller Blinds Discount Card</title>
<link href="https://fonts.googleapis.com/css2?family=Poppins:wght@300;400;600;700;800&family=Great+Vibes&display=swap" rel="stylesheet">
<style>
  :root {
    --blue: #2fa3e0;
    --blue-deep: #1a7fd1;
    --blue-pale: #e6f3fb;
    --ink: #2b2b2b;
    --grey: #6d6d6d;
    --grey-band: #eeeeee;
    --paper: #ffffff;
    --stage: #d9dde1;
  }
  * { box-sizing: border-box; margin: 0; padding: 0; }
  html, body { width: 1200px; height: 910px; overflow: hidden; }
  body {
    background: var(--stage);
    font-family: "Poppins", sans-serif;
    display: flex;
    align-items: center;
    justify-content: center;
    gap: 40px;
  }
  .card {
    position: relative;
    width: 540px;
    height: 330px;
    background: var(--paper);
    overflow: hidden;
    box-shadow: 0 6px 18px rgba(0,0,0,.18);
  }

  /* ---------- Offer side ---------- */
  .offer-grey-band {
    position: absolute; left: 0; right: 0; bottom: 58px; height: 34px;
    background: var(--grey-band);
  }
  .offer-headline {
    position: absolute; top: 22px; left: 0; right: 0;
    display: flex; align-items: center; justify-content: center; gap: 12px;
  }
  .offer-headline .rule { width: 46px; height: 7px; border-top: 2px solid var(--blue); border-bottom: 2px solid var(--blue); }
  .offer-headline h2 {
    font-weight: 800; font-size: 44px; letter-spacing: 2px; color: var(--blue); line-height: 1;
  }
  .offer-sub {
    position: absolute; top: 76px; left: 0; right: 0; text-align: center;
    font-weight: 300; font-size: 12px; color: var(--grey); line-height: 1.35;
  }
  .badge { position: absolute; top: 112px; width: 124px; height: 124px; }
  .badge svg { position: absolute; inset: 0; }
  .badge-text {
    position: absolute; inset: 0; display: flex; flex-direction: column;
    align-items: center; justify-content: center; gap: 2px; color: #fff; text-align: center;
    font-weight: 700; font-size: 11px; line-height: 1.15;
  }
  .badge-text small { font-weight: 400; font-size: 7.5px; letter-spacing: .4px; line-height: 1.25; }
  .badge-measure { left: 78px; }
  .badge-price   { left: 208px; }
  .badge-family  { left: 338px; }
  .offer-call {
    position: absolute; left: 0; right: 0; bottom: 0; height: 58px;
    background: var(--blue);
    display: flex; align-items: center; justify-content: center; gap: 8px;
    color: #fff; font-size: 21px; font-weight: 400; letter-spacing: 1px;
  }
  .offer-call strong { font-weight: 700; }

  /* ---------- Brand side ---------- */
  .brand-title {
    position: absolute; top: 14px; left: 22px;
    font-weight: 800; font-size: 52px; color: var(--blue); line-height: 1; letter-spacing: 1px;
  }
  .brand-tagline {
    position: absolute; top: 72px; left: 24px;
    font-weight: 400; font-size: 23px; color: var(--ink);
  }
  .brand-photo { position: absolute; left: 22px; top: 114px; width: 290px; height: 138px; }
  .brand-phone {
    position: absolute; left: 22px; top: 252px; width: 290px; height: 34px;
    background: var(--blue); color: #fff;
    display: flex; align-items: center; padding-left: 14px; gap: 8px;
    font-size: 19px; letter-spacing: 1px;
  }
  .brand-phone strong { font-weight: 700; }
  .brand-name {
    position: absolute; left: 22px; bottom: 12px;
    display: flex; align-items: center; gap: 8px;
    font-weight: 600; font-size: 15px; color: var(--blue); letter-spacing: 1px;
  }
  .brand-name .mark { width: 14px; height: 14px; background: var(--blue); }
  .brand-bubble {
    position: absolute; right: 26px; top: 172px; width: 170px; height: 116px;
  }
  .brand-bubble svg { position: absolute; inset: 0; }
  .brand-bubble p {
    position: absolute; inset: 0; display: flex; align-items: center; justify-content: center;
    text-align: center; font-family: "Great Vibes", cursive; font-size: 25px; color: #fff;
    line-height: 1; padding: 0 22px 10px;
  }
  .brand-accent {
    position: absolute; right: 0; top: 114px; width: 200px; height: 40px; background: var(--grey-band);
  }
</style>
</head>
<body>

  <section class="card card-offer">
    <div class="offer-grey-band"></div>
    <div class="offer-headline">
      <span class="rule"></span><h2>25% OFF</h2><span class="rule"></span>
    </div>
    <p class="offer-sub">Quality Custom Made Roller Blinds<br>Blockout - screen - LightFiltering</p>

    <div class="badge badge-measure">
      <svg viewBox="0 0 100 100"><polygon fill="#3aa7e6" points="50,2 55,8 62,4 65,11 73,9 74,17 82,17 81,25 89,27 86,34 93,38 88,44 94,50 88,56 93,62 86,66 89,73 81,75 82,83 74,83 73,91 65,89 62,96 55,92 50,98 45,92 38,96 35,89 27,91 26,83 18,83 19,75 11,73 14,66 7,62 12,56 6,50 12,44 7,38 14,34 11,27 19,25 18,17 26,17 27,9 35,11 38,4 45,8"/><circle cx="50" cy="50" r="37" fill="#58b8ee" stroke="#fff" stroke-width="1.5"/></svg>
      <div class="badge-text">FREE in Home<small>MEASURE<br>&amp; QUOTE</small></div>
    </div>
    <div class="badge badge-price">
      <svg viewBox="0 0 100 100"><polygon fill="#3aa7e6" points="50,2 55,8 62,4 65,11 73,9 74,17 82,17 81,25 89,27 86,34 93,38 88,44 94,50 88,56 93,62 86,66 89,73 81,75 82,83 74,83 73,91 65,89 62,96 55,92 50,98 45,92 38,96 35,89 27,91 26,83 18,83 19,75 11,73 14,66 7,62 12,56 6,50 12,44 7,38 14,34 11,27 19,25 18,17 26,17 27,9 35,11 38,4 45,8"/><circle cx="50" cy="50" r="37" fill="#58b8ee" stroke="#fff" stroke-width="1.5"/></svg>
      <div class="badge-text">Best Price<small>GUARANTEE</small></div>
    </div>
    <div class="badge badge-family">
      <svg viewBox="0 0 100 100"><polygon fill="#3aa7e6" points="50,2 55,8 62,4 65,11 73,9 74,17 82,17 81,25 89,27 86,34 93,38 88,44 94,50 88,56 93,62 86,66 89,73 81,75 82,83 74,83 73,91 65,89 62,96 55,92 50,98 45,92 38,96 35,89 27,91 26,83 18,83 19,75 11,73 14,66 7,62 12,56 6,50 12,44 7,38 14,34 11,27 19,25 18,17 26,17 27,9 35,11 38,4 45,8"/><circle cx="50" cy="50" r="37" fill="#58b8ee" stroke="#fff" stroke-width="1.5"/></svg>
      <div class="badge-text">Family<small>OWNED &amp;<br>OPERATED</small></div>
    </div>

    <div class="offer-call">CALL <strong>0400 123 987</strong> TODAY!</div>
  </section>

  <section class="card card-brand">
    <div class="brand-accent"></div>
    <h1 class="brand-title">ROLLER BLINDS</h1>
    <p class="brand-tagline">FREE in Home Meacure &amp; Quote</p>
    <svg class="brand-photo" role="img" aria-label="Photo of a room with roller blinds over glass doors looking onto a garden" viewBox="0 0 290 138" preserveAspectRatio="none">
      <defs>
        <linearGradient id="photoTone" x1="0" y1="0" x2="1" y2="1">
          <stop offset="0" stop-color="#7a6a5e"/>
          <stop offset=".5" stop-color="#6f8a5a"/>
          <stop offset="1" stop-color="#9a8f86"/>
        </linearGradient>
      </defs>
      <rect width="290" height="138" fill="url(#photoTone)"/>
    </svg>
    <div class="brand-phone"><strong>0400 123 987</strong> TODAY!</div>
    <div class="brand-name"><span class="mark"></span>K&amp;M INTERIORS</div>
    <div class="brand-bubble">
      <svg viewBox="0 0 170 116">
        <defs>
          <linearGradient id="bubbleTone" x1="0" y1="0" x2="1" y2="1">
            <stop offset="0" stop-color="#6cc6f2"/>
            <stop offset="1" stop-color="#1a6fd6"/>
          </linearGradient>
        </defs>
        <path d="M85 6 C132 6 164 28 164 54 C164 80 132 100 85 100 C70 100 56 98 44 94 L18 112 L26 86 C12 77 6 66 6 54 C6 28 38 6 85 6 Z" fill="url(#bubbleTone)"/>
      </svg>
      <p>Huge Selection of Fabrics</p>
    </div>
  </section>

</body>
</html>
```